Quick Straightforward Billboard Redesign

- Design billboard sized for 10 foot' x 36' foot width live area size and please include bleeds 6" around all sides
- Exact blue color match is imperative in headline, logo, phone number bubble or wherever used. C-83 / M-45 / Y-1 / K-0-
- What I hope to illustrate is that our company offers the best porch screening in the area area, in regards to quality, expertise, durability, storms proof, but we do not build screen porches.
- Current board is attached below from previous designer, and as you can see sizing was off, white space on edges make it appear to be sized incorrectly.
- I also attached my own little mock up idea well well if it helps, favorite image, logo, headline, etc and ideas perhaps on expanding or making this better?

Thanks so much!

Target Market(s)

Drivers and passengers, Southeastern NC, are of immense new construction and high end homes.

Industry/Entity Type

Construction

Colors
0054AA
0677BA
7BADD7
CADEEF
E8F1F8

Requirements
Must have
• Blue color matching
Nice to have
• Design spins or other thoughts on my little mock up

```html
<!DOCTYPE html>
<html lang="en">
<head>
<meta charset="utf-8">
<title>Tidewater Screening Billboard</title>
<link rel="stylesheet" href="https://fonts.googleapis.com/css2?family=Bebas+Neue&family=Oswald:wght@400;500&display=swap">
<style>
  :root {
    --page-bg: #e4e4e4;
    --board-white: #ffffff;
    --brand-blue: #0677ba;
    --name-blue: #1468b3;
    --headline-blue: #1e80c1;
    --headline-teal: #1f9a9a;
    --headline-green: #25ad6a;
    --band-blue: #1a78c0;
    --band-green: #22b463;
    --rule-blue: #2a86c4;
    --divider: #d6d6d6;
    --band-text: #ffffff;
  }
  * { margin: 0; padding: 0; box-sizing: border-box; }
  html, body {
    width: 1200px;
    height: 420px;
    overflow: hidden;
    background: var(--page-bg);
  }
  .billboard {
    position: absolute;
    left: 20px;
    top: 49px;
    width: 1160px;
    height: 322px;
    background: var(--board-white);
  }
  .billboard__message {
    display: block;
    width: 1160px;
    height: 232px;
  }
  .billboard__contact-band {
    display: block;
    width: 1160px;
    height: 90px;
  }
  .brand-name {
    font-family: "Bebas Neue", "Oswald", sans-serif;
    font-size: 87px;
    fill: var(--name-blue);
  }
  .headline {
    font-family: "Bebas Neue", "Oswald", sans-serif;
    font-size: 90px;
  }
  .contact-text {
    font-family: "Oswald", "Arial Narrow", sans-serif;
    fill: var(--band-text);
  }
  .contact-text--web { font-size: 48px; font-weight: 400; }
  .contact-text--phone { font-size: 64px; font-weight: 500; }
</style>
</head>
<body>
  <main class="billboard">
    <svg class="billboard__message" viewBox="0 0 1160 232" aria-label="Tidewater Screening — Screen your porch. Built for the coast.">
      <defs>
        <linearGradient id="headline-gradient" gradientUnits="userSpaceOnUse" x1="573" y1="0" x2="1118" y2="0">
          <stop offset="0" stop-color="var(--headline-blue)"/>
          <stop offset="0.5" stop-color="var(--headline-teal)"/>
          <stop offset="1" stop-color="var(--headline-green)"/>
        </linearGradient>
      </defs>

      <rect class="brand-mark" x="58" y="56" width="130" height="130" fill="var(--brand-blue)"/>
      <text class="brand-name" x="217" y="102" textLength="287" lengthAdjust="spacingAndGlyphs">TIDEWATER</text>
      <text class="brand-name" x="217" y="188" textLength="287" lengthAdjust="spacingAndGlyphs">SCREENING</text>

      <line class="divider" x1="539" y1="44" x2="539" y2="191" stroke="var(--divider)" stroke-width="1.5"/>

      <text class="headline" x="573" y="105" fill="url(#headline-gradient)" textLength="545" lengthAdjust="spacingAndGlyphs">SCREEN YOUR PORCH.</text>
      <line class="headline__rule" x1="575" y1="115" x2="1118" y2="115" stroke="url(#headline-gradient)" stroke-width="1"/>
      <text class="headline" x="575" y="188" fill="url(#headline-gradient)" textLength="543" lengthAdjust="spacingAndGlyphs">BUILT FOR THE COAST.</text>
      <line class="headline__rule" x1="575" y1="197" x2="1118" y2="197" stroke="url(#headline-gradient)" stroke-width="1"/>
    </svg>

    <svg class="billboard__contact-band" viewBox="0 0 1160 90" aria-label="www.tidewaterscreening.com — Call us 910.555.0142">
      <defs>
        <linearGradient id="band-gradient" x1="0" y1="0" x2="1" y2="0">
          <stop offset="0" stop-color="var(--band-blue)"/>
          <stop offset="1" stop-color="var(--band-green)"/>
        </linearGradient>
      </defs>
      <rect class="band" width="1160" height="90" fill="url(#band-gradient)"/>

      <text class="contact-text contact-text--web" x="43" y="61" textLength="460" lengthAdjust="spacingAndGlyphs">www.tidewaterscreening.com</text>

      <g class="phone-icon" transform="translate(600 45)">
        <circle r="24" fill="var(--brand-blue)"/>
        <path d="M-9.5 -9.5 c-2 2 -2.5 5 -0.5 9 c2.5 5 6 8.5 10.5 10.8 c3.5 1.7 6.5 1.2 8.5 -0.8 l1 -1 c0.8 -0.8 0.8 -2 0 -2.7 l-3.2 -3 c-0.8 -0.7 -2 -0.7 -2.7 0 l-1.6 1.6 c-3 -1.5 -5.5 -4 -7 -7 l1.6 -1.6 c0.7 -0.7 0.7 -1.9 0 -2.7 l-3 -3.2 c-0.7 -0.8 -1.9 -0.8 -2.7 0 z" fill="#ffffff"/>
        <path d="M1.5 -8 a7 7 0 0 1 6.5 6.5" fill="none" stroke="#ffffff" stroke-width="2" stroke-linecap="round"/>
        <path d="M2 -13 a12 12 0 0 1 11 11" fill="none" stroke="#ffffff" stroke-width="2" stroke-linecap="round"/>
      </g>

      <text class="contact-text contact-text--phone" x="643" y="68" textLength="456" lengthAdjust="spacingAndGlyphs">Call us 910.555.0142</text>
    </svg>
  </main>
</body>
</html>
```